bRIDGE ON LLC - New Website Design Help!

Need to build a website that showcases our capabilities. We will be specializing in Government Contracting for SDVOSB set aside and sole source contracts. We provide many services such as Audio & Visual design, install, consulting, all the way through to project completion. Also, IT/Voice infrastructure consulting, design, implementation, project management all the way to project completion.

Target Market(s)

IT/Voice Government Contracts, Managed Service Contracts for Government

Industry/Entity Type

Information Technology and Telecommunications

Coding

Coded - Design and coding required

Number of Pages Required

5+ page

Font styles to use
Other font styles liked:
• Calibri

Colors

Designer to choose only greyscale colors for use in the design.

Requirements
Must have
• Drop downs for additional pages, for About Us, Services, Industry Solutions, Our Company, Contact Us
Nice to have
• Testimonials page or Blog page

```html
<!DOCTYPE html>
<html lang="en">
<head>
<meta charset="utf-8">
<title>Bridge On LLC</title>
<link rel="stylesheet" href="https://fonts.googleapis.com/css2?family=Michroma&family=Lato:wght@400;700;900&family=Roboto+Condensed:wght@700&display=swap">
<style>
:root{
  --ink:#111111;
  --dark:#1c1c1c;
  --charcoal:#262626;
  --mid:#6d6d6d;
  --soft:#9a9a9a;
  --line:#d6d6d6;
  --pale:#ececec;
  --paper:#f4f4f4;
  --white:#ffffff;
}
*{margin:0;padding:0;box-sizing:border-box}
html,body{width:1200px;height:4758px;overflow:hidden;background:var(--white)}
body{font-family:'Lato',sans-serif;color:var(--ink);position:relative}
.abs{position:absolute}
section,header,footer{position:absolute;left:0;width:1200px;overflow:hidden}
.display{font-family:'Michroma',sans-serif;text-transform:uppercase;letter-spacing:1px;line-height:1.15}
.eyebrow{font-family:'Michroma',sans-serif;text-transform:uppercase;font-size:10px;letter-spacing:3px;color:var(--mid)}
.btn{position:absolute;display:flex;align-items:center;justify-content:center;font-size:10px;font-weight:700;text-transform:uppercase;letter-spacing:1px}
.btn-dark{background:var(--ink);color:var(--white)}
.btn-light{background:var(--white);color:var(--ink)}
.photo{position:absolute}
.topbar{top:0;height:96px;background:var(--pale)}
.brand{position:absolute;font-family:'Michroma',sans-serif;font-size:20px;font-weight:400;letter-spacing:1px;display:flex;align-items:center;gap:8px}
.brand .mark{width:14px;height:14px;background:currentColor}
.contact{position:absolute;top:22px;display:flex;align-items:center;gap:10px}
.contact svg{width:28px;height:28px}
.contact small{display:block;font-size:7px;letter-spacing:1px;color:var(--mid);text-transform:uppercase}
.contact span{font-size:9px;color:var(--ink)}
.nav{position:absolute;top:70px;left:229px;width:742px;height:52px;background:var(--white);z-index:3;display:flex;align-items:center;box-shadow:0 4px 16px rgba(0,0,0,.15)}
.nav a{font-size:9px;font-weight:700;text-transform:uppercase;color:var(--ink);text-decoration:none;letter-spacing:.5px}
.nav .quote{position:absolute;right:0;top:0;width:151px;height:52px;background:var(--charcoal);color:var(--white);display:flex;align-items:center;justify-content:center}
.hero{top:96px;height:524px;background:var(--dark)}
.hero .photo{inset:0;background:linear-gradient(90deg,#0d1218 0%,#1d2630 45%,#2d3640 70%,#141a21 100%)}
.service-card{position:absolute;top:127px;width:234px;height:368px;background:var(--white);box-shadow:0 2px 10px rgba(0,0,0,.06)}
.service-card .photo{left:0;top:0;width:234px;height:177px;background:linear-gradient(135deg,#2a2a2a,#5a5a5a 55%,#1a1a1a)}
.service-card h3{position:absolute;left:31px;top:202px;width:190px;font-size:13px;font-weight:700;line-height:1.35}
.service-card p{position:absolute;left:31px;top:254px;width:175px;font-size:9px;color:var(--soft);line-height:1.9}
.read{position:absolute;font-size:8px;font-weight:700;letter-spacing:2px;text-transform:uppercase;display:flex;align-items:center;gap:8px}
.read::after{content:"";width:14px;height:1px;background:var(--soft)}
.counter{position:absolute;top:80px}
.counter b{display:block;font-family:'Michroma',sans-serif;font-size:60px;font-weight:400;line-height:1}
.counter span{display:block;margin-top:18px;font-size:11px;color:var(--charcoal)}
.person{position:absolute;top:197px;text-align:left}
.person .photo{position:relative;width:48px;height:48px;border-radius:50%;background:radial-gradient(circle,#8a8a8a,#4a4a4a)}
.person h4{margin-top:22px;font-size:10px;font-weight:400;color:var(--white)}
.person small{font-size:7px;letter-spacing:1px;color:var(--soft);text-transform:uppercase}
.dim h4{color:#777}
.project{position:absolute;top:120px;width:234px;height:319px}
.project .photo{inset:0}
.project .label{position:absolute;left:13px;bottom:13px;width:208px;height:45px;background:var(--ink);color:var(--white);font-size:11px;font-weight:700;display:flex;align-items:center;justify-content:center}
.step{position:absolute;left:229px;display:flex;gap:22px;font-size:11px;color:#444;line-height:1.7}
.step i{flex:none;width:24px;height:24px;border-radius:50%;background:var(--ink);color:var(--white);font-style:normal;font-size:8px;font-weight:700;display:flex;align-items:center;justify-content:center;margin-top:6px}
.why-title{left:229px;top:131px;width:360px;font-size:13px;font-weight:400;line-height:1.7;letter-spacing:.3px;white-space:nowrap}
.post{position:absolute;top:135px;width:234px}
.post .photo{position:relative;height:175px}
.post .meta{margin-top:22px;font-size:8px;color:#444}
.post h3{margin-top:8px;font-size:14px;font-weight:700;line-height:1.6}
.post p{margin-top:18px;font-size:8px;color:var(--soft);line-height:2.2}
.post .read{position:relative;margin-top:18px}
.flinks a{display:block;font-size:9px;color:#bdbdbd;text-decoration:none;margin-bottom:16px}
</style>
</head>
<body>

<header class="topbar">
  <div class="brand" style="left:231px;top:28px;color:var(--ink)"><span class="mark"></span>BRIDGE ON</div>
  <div class="contact" style="left:552px">
    <svg viewBox="0 0 28 28"><circle cx="14" cy="14" r="13" fill="none" stroke="#555"/><rect x="8" y="10" width="12" height="8" fill="none" stroke="#333"/><path d="M8 10l6 5 6-5" fill="none" stroke="#333"/></svg>
    <div><small>Email</small><span>hello@bridgeonllc.net</span></div>
  </div>
  <div class="contact" style="left:716px">
    <svg viewBox="0 0 28 28"><circle cx="14" cy="14" r="13" fill="none" stroke="#555"/><path d="M10 8l3 3-2 2c1 2 2 3 4 4l2-2 3 3-2 2c-5 0-10-5-10-10z" fill="#333"/></svg>
    <div><small>Phone</small><span>555 210 4400</span></div>
  </div>
  <div class="contact" style="left:836px">
    <svg viewBox="0 0 28 28"><circle cx="14" cy="14" r="13" fill="none" stroke="#555"/><path d="M14 7a5 5 0 0 1 5 5c0 4-5 9-5 9s-5-5-5-9a5 5 0 0 1 5-5z" fill="#333"/><circle cx="14" cy="12" r="2" fill="#fff"/></svg>
    <div><small>Visit</small><span>218 Harbor Lane, USA</span></div>
  </div>
</header>

<nav class="nav">
  <a style="position:absolute;left:43px">Home</a>
  <a style="position:absolute;left:111px">About Us</a>
  <a style="position:absolute;left:203px">Services</a>
  <a style="position:absolute;left:290px">Solutions</a>
  <a style="position:absolute;left:385px">Testimonials</a>
  <a style="position:absolute;left:500px">Blog</a>
  <a class="quote">Get a Free Quote</a>
</nav>

<section class="hero">
  <div class="photo" role="img" aria-label="Engineers inspecting server racks in a dimly lit data centre"></div>
  <div class="abs" style="left:225px;top:152px;color:var(--white);font-size:11px;letter-spacing:.5px;text-transform:uppercase">Service Disabled Veteran Owned(SDVOSB)-Certified</div>
  <h1 class="display abs" style="left:227px;top:176px;color:var(--white);font-size:29px;font-weight:400;line-height:1.25">Empowering Government<br>Projects with Expertise</h1>
  <div class="abs" style="left:231px;top:266px;color:#d0d0d0;font-size:19px">Empowering Government Projects with Expertise</div>
  <div class="btn btn-light" style="left:229px;top:332px;width:140px;height:48px">Discover More</div>
  <svg class="abs" style="left:228px;top:458px" width="64" height="30" viewBox="0 0 64 30"><circle cx="15" cy="15" r="13" fill="none" stroke="#666"/><path d="M17 10l-5 5 5 5" fill="none" stroke="#888"/><circle cx="49" cy="15" r="13" fill="none" stroke="#ddd"/><path d="M47 10l5 5-5 5" fill="none" stroke="#fff"/></svg>
  <svg class="abs" style="left:960px;top:242px" width="12" height="40" viewBox="0 0 12 40"><circle cx="6" cy="5" r="4" fill="#fff"/><circle cx="6" cy="20" r="3.5" fill="none" stroke="#aaa"/><circle cx="6" cy="34" r="3.5" fill="none" stroke="#aaa"/></svg>
</section>

<section class="about" style="top:620px;height:593px;background:var(--white)">
  <div class="abs" style="left:0;top:0;width:356px;height:480px;background:linear-gradient(180deg,var(--paper),var(--white))"></div>
  <div class="photo" style="left:229px;top:76px;width:317px;height:380px;background:linear-gradient(160deg,#6f7c86,#a9b3ba 40%,#5c646b)" role="img" aria-label="Modern office with a wall monitor showing analytics and green plants"></div>
  <div class="abs" style="left:190px;top:325px;width:128px;height:159px;background:var(--ink);padding:6px"><div style="width:100%;height:100%;background:var(--white)"></div></div>
  <div class="eyebrow abs" style="left:607px;top:93px;color:var(--ink)">Welcome to Bridge On</div>
  <h2 class="display abs" style="left:607px;top:107px;font-size:24px;font-weight:400;line-height:1.18">We are leader in IT<br>communications</h2>
  <p class="abs" style="left:610px;top:181px;width:360px;font-size:8.5px;color:var(--mid);line-height:2.2">There are many variations of passages of Lorem Ipsum available, but the majority have suffered alteration in some form, by injected humour, or randomised words which don't look even slightly believable. If you are going to use a passage of Lorem Ipsum, you need to be sure there isn't anything embarrassing hidden in the middle of text.</p>
  <ul class="abs" style="left:609px;top:294px;list-style:none;font-size:10px;color:#333">
    <li style="height:25px;display:flex;gap:12px;align-items:center"><svg width="10" height="10" viewBox="0 0 10 10"><circle cx="5" cy="5" r="5"/><path d="M2.5 5l2 2 3-4" fill="none" stroke="#fff" stroke-width="1.3"/></svg>The best IT communication company</li>
    <li style="height:25px;display:flex;gap:12px;align-items:center"><svg width="10" height="10" viewBox="0 0 10 10"><circle cx="5" cy="5" r="5"/><path d="M2.5 5l2 2 3-4" fill="none" stroke="#fff" stroke-width="1.3"/></svg>We provide you the highest quality works</li>
    <li style="height:25px;display:flex;gap:12px;align-items:center"><svg width="10" height="10" viewBox="0 0 10 10"><circle cx="5" cy="5" r="5"/><path d="M2.5 5l2 2 3-4" fill="none" stroke="#fff" stroke-width="1.3"/></svg>Building creative &amp; professional</li>
    <li style="height:25px;display:flex;gap:12px;align-items:center"><svg width="10" height="10" viewBox="0 0 10 10"><circle cx="5" cy="5" r="5"/><path d="M2.5 5l2 2 3-4" fill="none" stroke="#fff" stroke-width="1.3"/></svg>We design industry materials of innovation</li>
  </ul>
  <div class="btn btn-dark" style="left:609px;top:438px;width:128px;height:46px;font-family:'Michroma',sans-serif;font-weight:400;font-size:8px">Learn More</div>
</section>

<section class="services" style="top:1213px;height:547px;background:var(--pale)">
  <div class="eyebrow abs" style="left:0;width:1200px;text-align:center;top:42px">Our Services</div>
  <h2 class="display abs" style="left:0;width:1200px;text-align:center;top:58px;font-size:30px;font-weight:400">What we offer</h2>
  <article class="service-card" style="left:229px">
    <div class="photo" role="img" aria-label="Technician installing equipment in a server rack"></div>
    <h3>Audio &amp; Visual Design, Installation, and Consulting</h3>
    <p>There are many variations of passages of available but the have alteration in that some form by injected.</p>
    <div class="read" style="left:31px;top:334px">Read More</div>
  </article>
  <article class="service-card" style="left:482px">
    <div class="photo" role="img" aria-label="Engineer with laptop in a data centre aisle"></div>
    <h3 style="top:198px">IT/Voice Infrastructure Consulting,Implementation</h3>
    <p>There are many variations of passages of available but the have alteration in that some form by injected.</p>
    <div class="read" style="left:31px;top:330px">Read More</div>
  </article>
  <article class="service-card" style="left:735px">
    <div class="photo" role="img" aria-label="Two engineers reviewing a tablet beside server cabinets"></div>
    <h3>Complete Project Management in Audio/Video</h3>
    <p>There are many variations of passages of available but the have alteration in that some form by injected.</p>
    <div class="read" style="left:31px;top:334px">Read More</div>
  </article>
</section>

<section class="stats" style="top:1760px;height:243px;background:var(--white)">
  <div class="counter" style="left:234px"><b>84</b><span>Projects are Completed</span></div>
  <div class="counter" style="left:443px"><b>22</b><span>Professional Contractors</span></div>
  <div class="counter" style="left:675px"><b>17</b><span>Industries Served</span></div>
  <div class="counter" style="left:858px"><b>88</b><span>Happy Customers</span></div>
</section>

<section class="testimonials" style="top:2003px;height:397px;background:var(--charcoal)">
  <div class="display abs" style="left:0;width:1200px;text-align:center;top:-10px;font-size:44px;letter-spacing:28px;color:#333">Testimonials</div>
  <div class="eyebrow abs" style="left:229px;top:105px;color:#bbb">Our Testimonails</div>
  <h2 class="display abs" style="left:229px;top:124px;color:var(--white);font-size:30px;font-weight:400">Happy Customers</h2>
  <svg class="abs" style="left:935px;top:113px" width="36" height="10" viewBox="0 0 36 10"><circle cx="5" cy="5" r="4" fill="#fff"/><circle cx="17" cy="5" r="3.5" fill="#888"/><circle cx="29" cy="5" r="3.5" fill="#888"/></svg>
  <div class="person" style="left:229px"><div class="photo" role="img" aria-label="Client portrait"></div><h4>Dana Price</h4><small>Director</small></div>
  <div class="person dim" style="left:325px"><div class="photo" role="img" aria-label="Client portrait" style="opacity:.5"></div><h4>Mark Ellis</h4><small>Director</small></div>
  <div class="person dim" style="left:419px"><div class="photo" role="img" aria-label="Client portrait" style="opacity:.5"></div><h4>Nora Quinn</h4><small>Director</small></div>
  <p class="abs" style="left:546px;top:193px;width:430px;color:var(--white);font-size:12.5px;line-height:2.15">“This is due to their excellent service competitive pricing and customer support. It's throughly refresing to get such a personal touch. There are many variations of passages of available, but the majority have suffered alteration in some form by injected humour.”</p>
  <div class="abs" style="left:546px;top:309px;color:#ccc;font-size:9px;letter-spacing:2px">25 NOV, 2019</div>
</section>

<section class="projects" style="top:2400px;height:590px;background:var(--white)">
  <div class="abs" style="left:844px;top:0;width:356px;height:300px;background:linear-gradient(180deg,var(--paper),var(--white))"></div>
  <div class="eyebrow abs" style="left:0;width:1200px;text-align:center;top:36px;font-family:'Lato',sans-serif;font-size:9px">Our Projects</div>
  <h2 class="abs" style="left:0;width:1200px;text-align:center;top:54px;font-family:'Roboto Condensed',sans-serif;font-size:30px;font-weight:700">Explore Recent Work</h2>
  <div class="project" style="left:229px"><div class="photo" role="img" aria-label="Glowing globe held in cupped hands" style="background:radial-gradient(circle at 50% 45%,#b9c6d1,#4e5c6a 45%,#101418)"></div><div class="label">Project name goes here</div></div>
  <div class="project" style="left:483px"><div class="photo" role="img" aria-label="Bright blue-lit data centre corridor" style="background:linear-gradient(180deg,#2b3a48,#6d8396 50%,#1d2833)"></div>
    <div class="abs" style="left:14px;top:144px;width:206px;height:140px;background:var(--white);padding:18px 30px">
      <div style="font-size:11px;font-weight:700">Project Name goes here</div>
      <div style="margin-top:14px;font-size:8px;color:var(--soft);line-height:1.9">There are many new variations of available but majority text.</div>
      <div class="read" style="position:relative;margin-top:12px">Read More</div>
    </div>
  </div>
  <div class="project" style="left:737px"><div class="photo" role="img" aria-label="Server racks with a figure at the end of the aisle" style="background:linear-gradient(90deg,#1b232b,#55697a 50%,#1b232b)"></div><div class="label">Project name goes here</div></div>
  <div class="abs" style="left:231px;top:485px;width:12px;height:1px;background:#555"></div>
  <div class="btn btn-dark" style="left:530px;top:502px;width:140px;height:48px;font-size:9px">View All Projects</div>
</section>

<section class="why" style="top:2990px;height:536px;background:var(--pale)">
  <div class="eyebrow abs" style="left:229px;top:111px;color:#333">Why choose us</div>
  <h2 class="display abs why-title">We're the most trusted<br>udio &amp; visual design, install,<br>consulting company</h2>
  <div class="step" style="top:225px"><i>01</i><span>Solution for small and large businesses voloptatem<br>accusantium doloremque laudantium</span></div>
  <div class="step" style="top:282px"><i>02</i><span>We can help your business to siml andhne tnenn<br>accusantium doloremque laudantium</span></div>
  <div class="step" style="top:338px"><i>03</i><span>Best industrial safe solutions for furture lipsum<br>accusantium doloremque laudantium</span></div>
  <div class="btn btn-light" style="left:229px;top:410px;width:127px;height:48px;font-size:9px;text-transform:none">Learn More</div>
  <div class="photo" style="left:609px;top:0;width:591px;height:374px;background:radial-gradient(ellipse at 50% 40%,#8aa3b7,#304556 50%,#0e161d)" role="img" aria-label="Futuristic blue-lit server room with monitoring screens"></div>
  <div class="abs" style="left:609px;top:374px;width:591px;height:162px;background:#141414"></div>
  <div class="abs" style="left:609px;top:374px;width:33px;height:162px;background:var(--ink)"></div>
  <div class="abs" style="left:617px;top:500px;transform:rotate(-90deg);transform-origin:left top;color:var(--white);font-size:8px;letter-spacing:2px;text-transform:uppercase;white-space:nowrap">How we work</div>
  <div class="abs" style="left:685px;top:436px;color:var(--white);font-size:13px;font-weight:700;line-height:1.9">How do we work with our clients and<br>service providers</div>
</section>

<section class="news" style="top:3526px;height:587px;background:var(--white)">
  <div class="eyebrow abs" style="left:229px;top:64px;color:#333">Our recent news</div>
  <h2 class="display abs" style="left:229px;top:80px;font-size:20px;font-weight:400">Latest news &amp; artciles</h2>
  <div class="btn btn-dark" style="left:829px;top:55px;width:142px;height:48px;font-size:9px;text-transform:none">View All Posts</div>
  <article class="post" style="left:229px"><div class="photo" role="img" aria-label="Engineer working on a laptop beside a server rack" style="background:linear-gradient(135deg,#3c4650,#8a959e 50%,#232a30)"></div><div class="meta">06 April, 2019 &nbsp;• &nbsp; 3 Comments</div><h3>We believe in building long lasting our business relashions</h3><p>Lorem ipsum is simply free text used by copytyping refreshing. Neque porro est qui dolorem ipsum quia quaed inventore veritatis et quasi architecto beatae vitae dicta sunt explicabo.</p><div class="read">Read More</div></article>
  <article class="post" style="left:483px"><div class="photo" role="img" aria-label="Hand holding a glowing network of connected icons" style="background:radial-gradient(circle at 55% 45%,#8fa6b8,#26394a 55%,#0c1219)"></div><div class="meta">06 April, 2019 &nbsp;• &nbsp; 3 Comments</div><h3>We believe in building long lasting our business relashions</h3><p>Lorem ipsum is simply free text used by copytyping refreshing. Neque porro est qui dolorem ipsum quia quaed inventore veritatis et quasi architecto beatae vitae dicta sunt explicabo.</p><div class="read">Read More</div></article>
  <article class="post" style="left:736px"><div class="photo" role="img" aria-label="Glowing digital brain on a dark blue background" style="background:radial-gradient(circle at 50% 45%,#7e98ad,#1f3346 55%,#0a1118)"></div><div class="meta">06 April, 2019 &nbsp;• &nbsp; 3 Comments</div><h3>We believe in building long lasting our business relashions</h3><p>Lorem ipsum is simply free text used by copytyping refreshing. Neque porro est qui dolorem ipsum quia quaed inventore veritatis et quasi architecto beatae vitae dicta sunt explicabo.</p><div class="read">Read More</div></article>
</section>

<section class="cta" style="top:4113px;height:323px;background:#0f0f0f">
  <div class="photo" style="inset:0;background:radial-gradient(ellipse at 50% 50%,#2a2a2a,#141414 60%,#0a0a0a)" role="img" aria-label="Dark circuit board pattern"></div>
  <div class="eyebrow abs" style="left:0;width:1200px;text-align:center;top:101px;color:#ccc">Don't hesitate to contact us</div>
  <h2 class="display abs" style="left:0;width:1200px;text-align:center;top:117px;color:var(--white);font-size:21px;font-weight:400;line-height:1.3">For better future and business,<br>let's get started now</h2>
  <div class="btn btn-light" style="left:530px;top:201px;width:140px;height:48px;font-size:9px;text-transform:none">Discover More</div>
</section>

<footer class="footer" style="top:4436px;height:322px;background:var(--dark)">
  <div class="brand" style="left:229px;top:55px;color:var(--white);font-size:22px"><span class="mark"></span>BRIDGE ON</div>
  <p class="abs" style="left:229px;top:114px;width:270px;color:#ccc;font-size:11.5px;line-height:1.9">Lorem Ipsum is simply dummy text of the printing and typesetting industry.</p>
  <svg class="abs" style="left:229px;top:190px" width="90" height="10" viewBox="0 0 90 10"><circle cx="5" cy="5" r="3.5" fill="#ddd"/><circle cx="31" cy="5" r="3.5" fill="#ddd"/><circle cx="57" cy="5" r="3.5" fill="#ddd"/><circle cx="83" cy="5" r="3.5" fill="#ddd"/></svg>
  <div class="flinks abs" style="left:535px;top:57px"><a>Home</a><a>About us</a><a>Services</a><a>Solutions</a><a>Our Company</a></div>
  <div class="flinks abs" style="left:672px;top:57px"><a>Testimonials</a><a>Blog</a><a>Contact</a><a>Terms &amp; Conditions</a><a>Privacy Policy</a></div>
  <div class="abs" style="left:882px;top:55px;width:89px;height:106px;background:var(--white);padding:5px"><div style="width:100%;height:100%;border:3px solid var(--ink)"></div></div>
  <div class="abs" style="left:0;top:262px;width:1200px;height:1px;background:#333"></div>
  <div class="abs" style="left:0;width:1200px;text-align:center;top:282px;color:#aaa;font-size:8px">© Copyright 2024 Bridge On</div>
</footer>

</body>
</html>
```